Business Card Design

New business card design

Target Market(s)

Residential & Commercial Property Managers

Industry/Entity Type

Plumbing Services

Contact Information for Business Card

Name - Rowan Keddle, title - Director, Phone Number - 0431 286 517, email - rowan@tbk-plumbing.com.au, Company ABN - 73 215 904 386,

Font styles to use
Sans Serif

Colors
0054AA
0677BA
7BADD7
CADEEF
E8F1F8

```html
<!DOCTYPE html>
<html lang="en">
<head>
<meta charset="utf-8">
<title>TBK Plumbing Services – Business Card</title>
<link rel="stylesheet" href="https://fonts.googleapis.com/css2?family=Montserrat:wght@400;500;700&display=swap">
<style>
  :root {
    --bg: #e9ebee;
    --card-dark: #1f242c;
    --card-light: #ffffff;
    --ink: #1f242c;
    --on-dark: #ffffff;
    --blue: #0677ba;
  }
  * { margin: 0; padding: 0; box-sizing: border-box; }
  html, body { width: 1200px; height: 931px; overflow: hidden; }
  body {
    background: var(--bg);
    font-family: "Montserrat", sans-serif;
    position: relative;
  }
  .card {
    position: absolute;
    width: 720px;
    height: 410px;
    border-radius: 26px;
    box-shadow: 0 10px 28px rgba(0,0,0,0.18);
    overflow: hidden;
  }
  .card--front { left: 60px; top: 45px; background: var(--card-dark); }
  .card--back  { left: 420px; top: 476px; background: var(--card-light); }

  .company-name {
    position: absolute;
    display: flex;
    align-items: center;
    font-weight: 500;
    line-height: 1.1;
    white-space: nowrap;
  }
  .company-name__dot {
    flex: none;
    border-radius: 50%;
    background: var(--blue);
  }

  .card--front .company-name {
    left: 0; right: 0; top: 178px;
    justify-content: center;
    gap: 18px;
    font-size: 46px;
    color: var(--on-dark);
  }
  .card--front .company-name__dot { width: 22px; height: 22px; }

  .card--back .company-name {
    right: 48px; top: 64px;
    gap: 12px;
    font-size: 26px;
    color: var(--ink);
  }
  .card--back .company-name__dot { width: 14px; height: 14px; }

  .holder { position: absolute; left: 48px; top: 188px; color: var(--ink); }
  .holder__name { font-size: 30px; font-weight: 700; letter-spacing: 0.3px; }
  .holder__title { font-size: 17px; font-weight: 400; margin-top: 2px; }

  .divider {
    position: absolute;
    left: 48px; right: 48px; top: 258px;
    height: 2px;
    background: var(--ink);
  }

  .address {
    position: absolute;
    right: 48px; top: 196px;
    text-align: right;
    font-size: 15px;
    line-height: 1.35;
    color: var(--ink);
  }

  .contacts { position: absolute; left: 48px; top: 276px; list-style: none; }
  .contacts li {
    display: flex; align-items: center; gap: 12px;
    font-size: 16px; color: var(--ink);
    height: 27px;
  }
  .contacts svg { width: 18px; height: 18px; flex: none; }
  .contacts .abn-label { color: var(--blue); font-weight: 700; }
</style>
</head>
<body>

<section class="card card--front" aria-label="Card front">
  <p class="company-name"><span class="company-name__dot"></span>TBK Plumbing Services</p>
</section>

<section class="card card--back" aria-label="Card back">
  <p class="company-name"><span class="company-name__dot"></span>TBK Plumbing Services</p>

  <div class="holder">
    <p class="holder__name">Rowan Keddle</p>
    <p class="holder__title">Director</p>
  </div>

  <p class="address">27 Fernhill Drive<br>Ashgrove, QLD 4060</p>

  <div class="divider"></div>

  <ul class="contacts">
    <li>
      <svg viewBox="0 0 24 24" aria-hidden="true"><path fill="var(--blue)" d="M6.6 10.8a15 15 0 0 0 6.6 6.6l2.2-2.2a1 1 0 0 1 1-.25 11.4 11.4 0 0 0 3.6.57 1 1 0 0 1 1 1V20a1 1 0 0 1-1 1A17 17 0 0 1 3 4a1 1 0 0 1 1-1h3.5a1 1 0 0 1 1 1c0 1.250.2 2.45.57 3.6a1 1 0 0 1-.25 1z"/></svg>
      0431 286 517
    </li>
    <li>
      <svg viewBox="0 0 24 24" aria-hidden="true"><rect x="2" y="5" width="20" height="14" rx="2" fill="var(--blue)"/><path d="M3 6l9 7 9-7" fill="none" stroke="#fff" stroke-width="1.6"/></svg>
      rowan@tbk-plumbing.com.au
    </li>
    <li>
      <svg viewBox="0 0 24 24" aria-hidden="true"><circle cx="12" cy="12" r="10" fill="var(--blue)"/><path d="M2 12h20M12 2c3 3 3 17 0 20M12 2c-3 3-3 17 0 20" fill="none" stroke="#fff" stroke-width="1.3"/></svg>
      www.tbk-plumbing.com.au
    </li>
    <li><span><span class="abn-label">ABN</span> - 73 215 904 386</span></li>
  </ul>
</section>

</body>
</html>
```